Corbell Lending Partners - Real estate loans - need a business card with a logo

I need a logo and a business card that looks elegant - that looks as if it is a big stablish corporation - We do real estate loans, my goal is to brand myself with colors black background - gold or silver letters - some combination - Name of the company different color than the rest of the card -

```html
<!DOCTYPE html>
<html lang="en">
<head>
<meta charset="utf-8">
<title>Corbell Lending Partners – Business Card</title>
<link href="https://fonts.googleapis.com/css2?family=Arimo:wght@400;600;700&display=swap" rel="stylesheet">
<style>
  :root {
    --stage: #151515;
    --card: #1c1c1c;
    --card-back-dark: #161616;
    --card-back-light: #3a3a3a;
    --gold: #c9a566;
    --white: #f2f2f2;
  }
  * { margin: 0; padding: 0; box-sizing: border-box; }
  html, body { width: 1200px; height: 900px; overflow: hidden; background: var(--stage); }
  body { font-family: "Arimo", Arial, sans-serif; color: var(--white); }

  .card {
    position: absolute;
    left: 250px;
    width: 700px;
    height: 400px;
    border-radius: 2px;
    box-shadow: 0 18px 40px rgba(0,0,0,0.55);
    overflow: hidden;
  }
  .card--back { top: 30px; }
  .card--front { top: 470px; background: var(--card); }

  .back-pattern {
    position: absolute; inset: 0;
    background: linear-gradient(120deg, var(--card-back-light) 0%, #262626 45%, var(--card-back-dark) 100%);
  }
  .back-mark {
    position: absolute; left: 50%; top: 50%;
    transform: translate(-50%, -50%);
    display: flex; align-items: center; gap: 10px;
    padding: 10px 16px;
    background: #1a1a1a;
    color: var(--gold);
    font-weight: 600; font-size: 15px; letter-spacing: 2px;
    text-transform: uppercase;
  }
  .back-mark .mark-square { width: 12px; height: 12px; background: var(--gold); }

  .brand {
    position: absolute; left: 48px; top: 0; width: 260px; height: 100%;
    display: flex; flex-direction: column; align-items: center; justify-content: center;
    gap: 18px;
  }
  .brand-square { width: 22px; height: 22px; background: var(--white); }
  .brand-name {
    font-weight: 700; font-size: 30px; line-height: 1.15; letter-spacing: 1.5px;
    text-transform: uppercase; text-align: center; color: var(--white);
  }

  .divider {
    position: absolute; left: 345px; top: 115px;
    width: 2px; height: 190px; background: var(--gold);
  }

  .contact { position: absolute; left: 392px; top: 110px; }
  .contact-name {
    font-weight: 600; font-size: 27px; letter-spacing: 1px;
    text-transform: uppercase; color: var(--gold);
  }
  .contact-title { font-size: 17px; margin-top: 2px; }
  .contact-address { font-size: 17px; line-height: 1.3; margin-top: 16px; }
  .contact-list { list-style: none; margin-top: 10px; font-size: 17px; line-height: 1.45; }
  .contact-list li { display: flex; align-items: center; gap: 10px; }
  .contact-list svg { width: 13px; height: 13px; flex: none; }
</style>
</head>
<body>
  <section class="card card--back">
    <div class="back-pattern" role="img" aria-label="Repeating embossed monogram pattern in dark grey tones"></div>
    <div class="back-mark"><span class="mark-square"></span>Corbell Lending Partners</div>
  </section>

  <section class="card card--front">
    <div class="brand">
      <span class="brand-square"></span>
      <p class="brand-name">Corbell<br>Lending Partners</p>
    </div>

    <div class="divider"></div>

    <div class="contact">
      <h1 class="contact-name">Daniel Harrow</h1>
      <p class="contact-title">Founder</p>
      <p class="contact-address">418 Linden Avenue<br>Carver, OR 97015</p>
      <ul class="contact-list">
        <li>
          <svg viewBox="0 0 16 16" aria-hidden="true"><path fill="var(--gold)" d="M3.6 1.2l2.3 2.6-1.2 1.9c.9 2 2.6 3.7 4.6 4.6l1.9-1.2 2.6 2.3-1.3 2.5C7.2 13.6 2.4 8.8 1.1 3.5z"/></svg>
          555 014 2380
        </li>
        <li>
          <svg viewBox="0 0 16 16" aria-hidden="true"><rect x="1" y="3" width="14" height="10" fill="none" stroke="var(--gold)" stroke-width="1.5"/><path d="M1 3l7 5.5L15 3" fill="none" stroke="var(--gold)" stroke-width="1.5"/></svg>
          info@corbelllending.com
        </li>
        <li>
          <svg viewBox="0 0 16 16" aria-hidden="true"><g fill="none" stroke="var(--gold)" stroke-width="1.3"><circle cx="8" cy="8" r="6.5"/><ellipse cx="8" cy="8" rx="3" ry="6.5"/><path d="M1.5 8h13M2.5 4.8h11M2.5 11.2h11"/></g></svg>
          www.corbelllending.com
        </li>
      </ul>
    </div>
  </section>
</body>
</html>
```